Swiftcoinswap.com Mobile App

Swiftcoinswap.com is an online Beurea de change. They buy and sell currency from individuals and large corporations.

The app will compliment the main website of the company and focus on specific features as set out in our brief document. overall the design must be high-quality, easy navigate with a one finger operation and nice clean design.

This content is for the design of 3 screen

Loading screen
Homepage screen
Buy Currency for Branch Collection screen

attached is a full brief, but the loading screen will incorporate the logo and the home screen must allow easy navigation to 6 key button features that will enable you to go to each section of the app.

The winner will get to design the remaining screens of the app which are approx 15/18 further screens, based on the same layout.

If you can code the app as well into iPhone and Android, please make this known as well.
Updates

Hello,

For further inspritation for the Home screen, we quite like the interface on the uploaded image lumavo-home.jpg

So you slide left and right with your finger to the button, instead of a list format or something quite 2d. Almost 3d like interface maybe with an option to display all as a list?

See what sort of creativity can be achieved.

thanks

Target Market(s)

Consumers mainly aged between 25-60

Industry/Entity Type

It Company

Requirements
Must have
• good clean visually stunning appearance with apply shiny effect buttons and navigation

```html
<!DOCTYPE html>
<html lang="en">
<head>
<meta charset="utf-8">
<title>Swiftcoinswap.com – Home</title>
<link href="https://fonts.googleapis.com/css2?family=Bebas+Neue&family=Raleway:wght@300&family=Ubuntu:wght@400&display=swap" rel="stylesheet">
<style>
  :root {
    --ink-white: #f4f4f4;
    --panel-top: #2b2f36;
    --panel-bottom: #14171c;
    --panel-edge: #060708;
    --heading-band: #262a31;
    --body-text: #e9e9e9;
    --bar-light: #4a4c50;
    --bar-dark: #151618;
    --button-light: #3a3c40;
    --button-dark: #101113;
    --icon-grey: #8b8d91;
    --banner-red: #d8161a;
    --banner-light: #e9eaec;
  }
  * { box-sizing: border-box; margin: 0; padding: 0; }
  html, body { width: 800px; height: 1200px; overflow: hidden; }
  body {
    position: relative;
    background:
      radial-gradient(ellipse 420px 380px at 440px 200px, rgba(214,196,30,0.95), rgba(214,196,30,0) 100%),
      radial-gradient(ellipse 380px 420px at 40px 360px, rgba(222,108,26,0.95), rgba(222,108,26,0) 100%),
      radial-gradient(ellipse 300px 300px at 80px 40px, rgba(190,40,70,0.9), rgba(190,40,70,0) 100%),
      radial-gradient(ellipse 360px 480px at 20px 860px, rgba(46,150,200,0.9), rgba(46,150,200,0) 100%),
      radial-gradient(ellipse 500px 520px at 760px 880px, rgba(20,28,70,1), rgba(20,28,70,0) 100%),
      radial-gradient(ellipse 300px 400px at 800px 100px, rgba(30,30,12,0.95), rgba(30,30,12,0) 100%),
      linear-gradient(180deg, #8a4a20 0%, #6a3a40 50%, #1a2a5a 100%);
    font-family: "Ubuntu", sans-serif;
  }
  .brand {
    position: absolute; left: 0; width: 800px; top: 238px;
    text-align: center; color: var(--ink-white);
  }
  .brand-name {
    font-family: "Raleway", sans-serif; font-weight: 300;
    font-size: 92px; letter-spacing: -2px; line-height: 1;
  }
  .brand-tagline {
    margin-top: 34px; margin-left: 180px;
    font-family: "Raleway", sans-serif; font-weight: 300;
    font-size: 30px; letter-spacing: 1px;
  }
  .feature-panel {
    position: absolute; left: 72px; top: 467px; width: 638px; height: 552px;
    background: linear-gradient(180deg, var(--panel-top), var(--panel-bottom));
    border: 2px solid var(--panel-edge); border-radius: 4px;
    box-shadow: 0 4px 14px rgba(0,0,0,0.45), inset 0 1px 0 rgba(255,255,255,0.12);
  }
  .promo-banner {
    position: absolute; left: 11px; top: 10px; width: 614px; height: 170px;
    border: 3px solid #0c0d0f;
    background: linear-gradient(90deg, var(--banner-red) 0%, #b5b8bc 30%, var(--banner-light) 45%, #f2f2f2 70%, #c9ccd2 100%);
  }
  .panel-heading {
    position: absolute; left: 0; right: 0; top: 193px; height: 62px;
    background: var(--heading-band);
    border-top: 1px solid rgba(255,255,255,0.12);
    border-bottom: 1px solid rgba(255,255,255,0.12);
    font-family: "Bebas Neue", sans-serif; font-size: 37px; letter-spacing: 0.5px;
    color: var(--ink-white); line-height: 62px; padding-left: 13px;
  }
  .panel-copy {
    position: absolute; left: 14px; right: 20px; top: 274px;
    font-size: 19.6px; line-height: 26.2px; color: var(--body-text);
  }
  .nav-bar {
    position: absolute; left: 0; top: 1070px; width: 800px; height: 80px;
    background: linear-gradient(180deg, var(--bar-light) 0%, #2a2b2e 50%, var(--bar-dark) 100%);
    border-top: 1px solid #666; border-bottom: 1px solid #000;
  }
  .nav-circle {
    position: absolute; top: 1076px; width: 66px; height: 66px; border-radius: 50%;
    background: linear-gradient(180deg, #4c4e52, #1c1d20);
    border: 2px solid #111;
    box-shadow: inset 0 1px 0 rgba(255,255,255,0.2);
    display: flex; align-items: center; justify-content: center;
  }
  .nav-active {
    position: absolute; left: 200px; top: 1062px; width: 402px; height: 90px;
    background: linear-gradient(180deg, var(--button-light), var(--button-dark));
    border: 2px solid #050505; border-radius: 4px;
    box-shadow: 0 2px 8px rgba(0,0,0,0.6), inset 0 1px 0 rgba(255,255,255,0.18);
  }
  .nav-active .nav-circle { top: 10px; left: 12px; }
  .nav-label {
    position: absolute; left: 100px; right: 0; top: 0; line-height: 90px;
    text-align: center; padding-right: 80px;
    font-family: "Bebas Neue", sans-serif; font-size: 50px; color: var(--ink-white);
  }
</style>
</head>
<body>
  <header class="brand">
    <div class="brand-name">Swiftcoinswap</div>
    <div class="brand-tagline">CURRENCY SPECIALISTS</div>
  </header>

  <section class="feature-panel">
    <div class="promo-banner" role="img" aria-label="Promotional banner: currency symbols, zero percent commission offer and a smiling adviser"></div>
    <h1 class="panel-heading">The Leaders in Currency Exchange</h1>
    <p class="panel-copy">This is Photoshop's version &nbsp;of Lorem Ipsum. Proin gravida nibh vel velit auctor aliquet. Aenean sollicitudin, lorem quis bibendum auctor, nisi elit consequat ipsum, nec sagittis sem nibh id elit. Duis sed odio sit amet nibh vulputate cursus a sit amet mauris. Morbi accumsan ipsum velit. Nam nec tellus a odio tincidunt auctor a ornare odio. Sed non &nbsp;mauris vitae erat consequat auctor eu in elit. Class aptent taciti sociosqu ad litora torquent per conubia nostra, per inceptos himenaeos. Mauris in erat justo.</p>
  </section>

  <nav>
    <div class="nav-bar"></div>
    <div class="nav-circle" style="left:38px"><svg width="30" height="30" viewBox="0 0 30 30"><path d="M6 4v23M6 6h12v9H6M18 9h7l-3 4 3 4h-7" fill="none" stroke="var(--icon-grey)" stroke-width="2.4"/></svg></div>
    <div class="nav-circle" style="left:118px"><svg width="30" height="30" viewBox="0 0 30 30"><path d="M6 4v23M6 6h12v9H6M18 9h7l-3 4 3 4h-7" fill="none" stroke="var(--icon-grey)" stroke-width="2.4"/></svg></div>
    <div class="nav-circle" style="left:627px"><svg width="30" height="30" viewBox="0 0 30 30"><path d="M6 4v23M6 6h12v9H6M18 9h7l-3 4 3 4h-7" fill="none" stroke="var(--icon-grey)" stroke-width="2.4"/></svg></div>
    <div class="nav-circle" style="left:712px"><svg width="30" height="30" viewBox="0 0 30 30"><path d="M6 4v23M6 6h12v9H6M18 9h7l-3 4 3 4h-7" fill="none" stroke="var(--icon-grey)" stroke-width="2.4"/></svg></div>
    <div class="nav-active">
      <div class="nav-circle"><svg width="30" height="34" viewBox="0 0 30 34"><rect x="5" y="2" width="21" height="30" rx="2" fill="#e6e6e6"/><rect x="2" y="7" width="5" height="3" fill="#e6e6e6"/><rect x="2" y="15" width="5" height="3" fill="#e6e6e6"/><rect x="2" y="23" width="5" height="3" fill="#e6e6e6"/><circle cx="16" cy="13" r="4" fill="#222"/><path d="M9 25c1-5 13-5 14 0z" fill="#222"/></svg></div>
      <div class="nav-label">About Us</div>
    </div>
  </nav>
</body>
</html>
```